Dental Office Needs Exciting New Stationary

We need a stationary design that incorporates the logo that we already have and would like to keep the existing color scheme. We need something clean and professional. This is a Endodontic (root canals) office and must represent a dental specialist's office. I need a design for a business card, envelope, and letterhead that all coordinate. I would like the business card to incorporate the information in the business card sample that I am providing. I made the business card design myself but would like to see a better one.
Dental

```html
<!DOCTYPE html>
<html lang="en">
<head>
<meta charset="utf-8">
<title>Summit Endodontics Stationery</title>
<link href="https://fonts.googleapis.com/css2?family=Montserrat:wght@400;600&display=swap" rel="stylesheet">
<style>
  :root{
    --bg:#c9d3da;
    --paper:#f7f8f9;
    --paper-shade:#eceef0;
    --blue:#3a86c8;
    --blue-deep:#2f74b3;
    --blue-light:#4499d6;
    --ink:#5c6670;
    --muted:#9aa3ab;
  }
  *{box-sizing:border-box;margin:0;padding:0}
  html,body{width:1200px;height:1000px;overflow:hidden}
  body{background:linear-gradient(135deg,#dde4e9,var(--bg));font-family:"Montserrat",sans-serif;position:relative}
  .sheet{position:absolute;background:var(--paper);box-shadow:0 6px 14px rgba(40,60,80,.18)}
  .brand{display:flex;align-items:center;gap:6px;font-weight:600;color:var(--blue);text-transform:uppercase;letter-spacing:.04em;white-space:nowrap}
  .brand-dot{width:8px;height:8px;border-radius:50%;background:currentColor;flex:none}
  .brand.on-blue{color:#fff}
  .small{font-size:7px;color:var(--ink);line-height:1.6}

  .letterhead{left:60px;top:60px;width:300px;height:420px}
  .letterhead .brand{position:absolute;left:30px;top:34px;font-size:12px}
  .letterhead .footer{position:absolute;left:30px;right:30px;bottom:26px;display:flex;justify-content:space-between}

  .folder-cover{left:60px;top:510px;width:300px;height:420px}
  .folder-cover .band{position:absolute;left:90px;right:0;top:50px;height:50px;background:linear-gradient(90deg,var(--blue-light),var(--blue-deep));display:flex;align-items:center;padding-left:22px}
  .folder-cover .band .brand{font-size:13px}
  .folder-cover .brand.foot{position:absolute;left:24px;bottom:22px;font-size:9px}

  .envelope-open{left:400px;top:60px;width:340px;height:210px;overflow:hidden}
  .envelope-open .flap-liner{position:absolute;left:0;right:0;top:0;height:70px;background:linear-gradient(180deg,var(--blue-deep),var(--blue))}

  .envelope-front{left:780px;top:60px;width:360px;height:180px}
  .envelope-front .brand{position:absolute;left:22px;top:104px;font-size:10px}
  .envelope-front .return{position:absolute;left:22px;top:126px}

  .envelope-back{left:780px;top:270px;width:360px;height:180px;overflow:hidden}
  .envelope-back .flap{position:absolute;left:0;top:0;width:360px;height:80px}
  .envelope-back .brand{position:absolute;left:30px;top:26px;font-size:11px}

  .card{width:160px;height:90px;top:330px}
  .card-front{left:400px}
  .card-front .brand{position:absolute;left:22px;top:38px;font-size:9px}
  .card-back{left:580px}
  .card-back .tab{position:absolute;right:0;top:10px;width:40px;height:12px;background:var(--blue);color:#fff;font-size:6px;padding-left:6px;line-height:12px}
  .card-back .who{position:absolute;left:14px;top:28px}
  .card-back .who strong{font-weight:600;color:var(--blue)}
  .card-back .reach{position:absolute;left:14px;bottom:10px}

  .folder-open{left:400px;top:510px;width:740px;height:420px}
  .folder-open .spine{position:absolute;left:369px;top:0;bottom:0;width:2px;background:var(--paper-shade)}
  .folder-open .pocket{position:absolute;bottom:0;width:346px;height:150px;background:linear-gradient(180deg,var(--blue-light),var(--blue-deep))}
  .folder-open .pocket.left{left:12px;border-top-right-radius:26px}
  .folder-open .pocket.right{right:12px;border-top-left-radius:26px}
  .folder-open .pocket .brand{position:absolute;right:22px;bottom:26px;font-size:10px}
</style>
</head>
<body>

  <section class="sheet letterhead" aria-label="Letterhead">
    <div class="brand"><span class="brand-dot"></span>Summit Endodontics</div>
    <div class="footer small">
      <p>120 Harbor Lane, Dover, NY 10020</p>
      <p>(555) 014-2290<br>summitendo.example</p>
    </div>
  </section>

  <section class="sheet folder-cover" aria-label="Presentation folder cover">
    <div class="band"><div class="brand on-blue"><span class="brand-dot"></span>Summit Endodontics</div></div>
    <div class="brand foot"><span class="brand-dot"></span>Summit Endodontics</div>
  </section>

  <section class="sheet envelope-open" aria-label="Envelope, flap open">
    <div class="flap-liner"></div>
  </section>

  <section class="sheet envelope-front" aria-label="Envelope front">
    <div class="brand"><span class="brand-dot"></span>Summit Endodontics</div>
    <p class="return small">120 Harbor Lane, Dover, NY 10020</p>
  </section>

  <section class="sheet envelope-back" aria-label="Envelope back">
    <svg class="flap" viewBox="0 0 360 80" aria-hidden="true">
      <defs><linearGradient id="flapFill" x1="0" x2="1"><stop offset="0" stop-color="#2f74b3"/><stop offset="1" stop-color="#4499d6"/></linearGradient></defs>
      <path d="M0 0H360V40Q360 52 348 54L190 80H170L12 54Q0 52 0 40Z" fill="url(#flapFill)"/>
    </svg>
    <div class="brand on-blue"><span class="brand-dot"></span>Summit Endodontics</div>
  </section>

  <section class="sheet card card-front" aria-label="Business card front">
    <div class="brand"><span class="brand-dot"></span>Summit Endodontics</div>
  </section>

  <section class="sheet card card-back" aria-label="Business card back">
    <div class="tab">Call</div>
    <p class="who small"><strong>Dr. Alex Morgan, DDS</strong><br>Endodontic Specialist</p>
    <p class="reach small">(555) 014-2290 · hello@summitendo.example</p>
  </section>

  <section class="sheet folder-open" aria-label="Presentation folder, open">
    <div class="spine"></div>
    <div class="pocket left"></div>
    <div class="pocket right"><div class="brand on-blue"><span class="brand-dot"></span>Summit Endodontics</div></div>
  </section>

</body>
</html>
```